Harrowmere Freight, Project

Company Profile
Harrowmere Freight Sdn Bhd is a well established and experienced freight forwarder in Kuala Lumpur, Malaysia. We specialize in air and sea forwarding, Custom Brokerage and regulatory compliance services, inland transportation,
overseas freighting and warehousing and distribution management. With our dedicated qualified and experienced professionals, we are fully committed to serving our clients.

Our Mission
Based on the motto “Quick, Reliable and Polite”, Harrowmere Freight is dedicated to upholding the following three points corporate philosophy:
1. Adhering to the principle that “the customer always comes first”.
2. Contributing to the development of the local community.
3. Making it our duty to be responsible and sincere.

Our Edge
• One-Stop Logistics Solutions
• Extensive Network Throughout Malaysia
• Highly Qualified and Experienced Pool of Professionals
• Comprehensive IT Solutions
• Innovative and Customer-focused Solutions
• Flexible and Consistent in Managing Exceptions
• Total Supply Chain Visibility

Target Market(s)

We sell the logistics services to all the industry in Malaysia. (ONE Stop Logistics Solutions)

Industry/Entity Type

Logistic

Contact Information for Business Card

I want the back of the card to be white with the logo and slogan. i would like to see the logo on the front with the general info.

Requirements
Must have
• Name, Title, Office, Cell, Fax, Email, Address, Website
Nice to have
• Modern Design Business Card

```html
<!DOCTYPE html>
<html lang="en">
<head>
<meta charset="utf-8">
<title>Harrowmere Freight – Business Card</title>
<link href="https://fonts.googleapis.com/css2?family=Open+Sans:wght@400;600;700&display=swap" rel="stylesheet">
<style>
  :root {
    --page-bg: #e9ecef;
    --card-white: #ffffff;
    --brand-blue: #1a7cc4;
    --brand-blue-deep: #0f5f9e;
    --blue-light: #4fb0e6;
    --ink: #2b2b2b;
    --ink-soft: #555a60;
    --slogan-grey: #7a7d80;
    --on-blue: #ffffff;
  }
  * { box-sizing: border-box; margin: 0; padding: 0; }
  html, body { width: 1200px; height: 800px; overflow: hidden; }
  body {
    background: var(--page-bg);
    font-family: "Open Sans", Arial, sans-serif;
    display: flex;
    align-items: center;
    justify-content: center;
    gap: 40px;
  }
  .card {
    width: 540px;
    height: 309px;
    border-radius: 4px;
    box-shadow: 0 10px 28px rgba(0,0,0,.16);
    position: relative;
    overflow: hidden;
  }

  /* Front */
  .card-front {
    background: var(--card-white);
    color: var(--ink);
    padding: 30px 40px 24px;
    display: flex;
    flex-direction: column;
    align-items: center;
    text-align: center;
  }
  .brand {
    display: flex;
    align-items: center;
    gap: 8px;
    color: var(--brand-blue-deep);
    font-weight: 600;
    font-size: 15px;
  }
  .brand-dot {
    width: 12px; height: 12px;
    border-radius: 50%;
    background: var(--brand-blue);
  }
  .person { margin-top: 22px; }
  .person-name {
    color: var(--brand-blue);
    font-weight: 700;
    font-size: 24px;
    line-height: 1.1;
  }
  .person-title { font-size: 14px; font-weight: 600; margin-top: 2px; }
  .person-tel { font-size: 10px; color: var(--ink-soft); margin-top: 2px; }
  .company { margin-top: 20px; font-size: 8.5px; line-height: 1.6; color: var(--ink-soft); }
  .company-name { color: var(--brand-blue); font-weight: 700; }
  .label { color: var(--brand-blue); font-weight: 600; }
  .slogan-front {
    margin-top: auto;
    font-weight: 700;
    font-size: 17px;
    color: var(--slogan-grey);
    letter-spacing: .3px;
  }

  /* Back */
  .card-back {
    background: linear-gradient(135deg, var(--blue-light) 0%, var(--brand-blue) 50%, var(--brand-blue-deep) 100%);
    color: var(--on-blue);
    padding: 34px 36px 24px;
  }
  .services-heading {
    text-align: center;
    font-weight: 700;
    font-size: 15px;
  }
  .services-list {
    list-style: none;
    margin-top: 12px;
    font-size: 11.5px;
    line-height: 1.75;
    text-align: center;
  }
  .services-list span::before { content: "• "; }
  .back-brand {
    position: absolute;
    left: 0; right: 0; bottom: 58px;
    display: flex;
    justify-content: center;
    align-items: center;
    gap: 8px;
    font-size: 15px;
    font-weight: 600;
    color: rgba(255,255,255,.75);
  }
  .back-brand .brand-dot { background: rgba(255,255,255,.75); }
  .slogan-back {
    position: absolute;
    left: 0; right: 0; bottom: 22px;
    text-align: center;
    font-weight: 700;
    font-size: 15px;
    color: rgba(255,255,255,.9);
    letter-spacing: .3px;
  }
</style>
</head>
<body>
  <section class="card card-front">
    <div class="brand"><span class="brand-dot"></span>Harrowmere Freight</div>
    <div class="person">
      <div class="person-name">Faris Hakimi</div>
      <div class="person-title">Managing Director</div>
      <div class="person-tel">Tel: +6012 418 2075</div>
    </div>
    <div class="company">
      <div class="company-name">HARROWMERE FREIGHT SDN BHD (1207344-K)</div>
      <div><span class="label">Address:</span> No. 14B, 2nd Floor, Jalan Seri Damai 3, Taman Damai Jaya, 41050 Klang, Selangor Darul Ehsan, Malaysia</div>
      <div><span class="label">Tel:</span> (603) 3342 1186 / 1187 • <span class="label">Fax:</span> (603) 3342 1190 • <span class="label">Email:</span> faris.hakimi@harrowmere.com.my</div>
      <div><span class="label">Website:</span> www.harrowmere.com.my</div>
    </div>
    <div class="slogan-front">ONE STOP LOGISTICS SOLUTIONS</div>
  </section>

  <section class="card card-back">
    <h2 class="services-heading">We're Specialize In</h2>
    <ul class="services-list">
      <li><span>International Shipping (Air/Sea)</span> <span>Supply Chain Management</span></li>
      <li><span>Tax Exemption Consultancy</span> <span>Transportation /Haulage</span> <span>Packing</span></li>
      <li><span>Consolidation – NVOCC</span> <span>Project Management</span> <span>Marine Insurance</span></li>
      <li><span>Warehousing</span> <span>Distribution</span> <span>Custom Brokerage</span> <span>Door to Door</span></li>
    </ul>
    <div class="back-brand"><span class="brand-dot"></span>Harrowmere Freight</div>
    <div class="slogan-back">ONE STOP LOGISTICS SOLUTIONS</div>
  </section>
</body>
</html>
```